Modern, clean business card for Clearbrook Optics

Updated business card with a modern look.

Logo on the front
Dr Tavin R Marquell and Associates on the front.
Three locations on the back:
Ridgefront Brantmart
509-555-0142
18342 E Fernhollow Ave

Pelham Brantmart
509-555-0187
4716 W Dunmore Ave

Copper Bluff Brantmart
509-555-0163
3854 S Kettering Rd

Facebook icon. www.clearbrookoptix.example

Nice open white space on back for writing next appointment time.

Target Market(s)

Main target is female 25-50, but I would like broad appeal.

Industry/Entity Type

Healthcare

Contact Information for Business Card

Modern look

Font styles to use
Serif

Requirements
Must have
• Logo and Dr Tavin R Marquell and Associates on front.
• 3 locations on back
• white space for noting next appointment

```html
<!DOCTYPE html>
<html lang="en">
<head>
<meta charset="utf-8">
<title>Clearbrook Optics – Business Card</title>
<link href="https://fonts.googleapis.com/css2?family=Questrial&display=swap" rel="stylesheet">
<style>
  :root {
    --backdrop: #b3b3b3;
    --card: #f2f2f2;
    --card-edge: #e3e3e3;
    --navy: #1f2d5c;
    --blue: #0f6fae;
    --grey-text: #9a9a9a;
    --rule: #9c9c9c;
    --band-grey: #8f8f8f;
    --white: #ffffff;
  }
  * { margin: 0; padding: 0; box-sizing: border-box; }
  html, body { width: 1200px; height: 1050px; overflow: hidden; }
  body {
    background: var(--backdrop);
    font-family: "Questrial", "Century Gothic", sans-serif;
    position: relative;
  }
  .card {
    position: absolute;
    left: 264px;
    width: 672px;
    height: 383px;
    background: radial-gradient(ellipse at 50% 35%, var(--white) 0%, var(--card) 60%, var(--card-edge) 100%);
    box-shadow: 0 4px 10px rgba(0,0,0,0.25);
    overflow: hidden;
  }
  .card--front { top: 111px; }
  .card--back { top: 574px; }

  .brand {
    position: absolute;
    display: flex;
    align-items: center;
    gap: 10px;
    color: var(--navy);
    white-space: nowrap;
  }
  .brand__dot { border-radius: 50%; background: var(--blue); }
  .card--front .brand { right: 44px; top: 120px; font-size: 30px; }
  .card--front .brand__dot { width: 22px; height: 22px; }
  .card--back .brand { right: 36px; top: 72px; font-size: 20px; }
  .card--back .brand__dot { width: 14px; height: 14px; }

  .doctor { position: absolute; left: 44px; top: 200px; }
  .doctor__name { font-size: 23px; color: var(--navy); line-height: 1.2; }
  .doctor__role { font-size: 15px; color: var(--grey-text); }

  .location { position: absolute; top: 274px; font-size: 14px; line-height: 19px; white-space: nowrap; }
  .location--ridgefront { left: 44px; }
  .location--pelham { left: 247px; }
  .location--copper { left: 433px; }
  .location__name { font-size: 17px; color: var(--navy); line-height: 22px; }
  .location__phone, .location__address { color: var(--grey-text); }
  .location__phone b { color: var(--navy); font-weight: normal; }

  .front-band { position: absolute; left: 0; top: 355px; width: 672px; height: 28px; }
  .front-band__url {
    position: absolute; left: 44px; top: 360px;
    color: var(--white); font-size: 14px; line-height: 18px; white-space: nowrap;
  }

  .reminder__title {
    position: absolute; left: 38px; top: 46px;
    font-size: 21px; font-weight: normal; letter-spacing: 2.5px; color: var(--navy);
  }
  .field {
    position: absolute; left: 38px; width: 598px;
    border-bottom: 2px solid var(--rule);
    font-size: 17px; letter-spacing: 2px; color: var(--navy);
    height: 24px; line-height: 20px;
  }
  .field--name { top: 124px; }
  .field--date { top: 166px; }
  .field--purpose { top: 209px; }
  .field__time { position: absolute; left: 368px; }

  .days {
    position: absolute; top: 254px; left: 0; width: 672px; height: 28px;
    list-style: none;
  }
  .day {
    position: absolute; top: 0; display: flex; align-items: center; gap: 14px;
    font-size: 17px; letter-spacing: 2px; color: var(--navy);
  }
  .day__box { width: 28px; height: 28px; border: 1.5px solid var(--rule); background: var(--white); }
  .day--mon { left: 85px; }
  .day--tue { left: 196px; }
  .day--wed { left: 306px; }
  .day--thu { left: 418px; }
  .day--fri { left: 529px; }

  .back-url {
    position: absolute; top: 294px; left: 0; width: 672px;
    text-align: center; font-size: 16px; color: var(--navy);
  }
  .back-rule { position: absolute; top: 322px; left: 0; width: 672px; height: 5px; background: var(--band-grey); }
  .back-band {
    position: absolute; top: 327px; left: 0; width: 672px; height: 56px;
    background: linear-gradient(90deg, var(--navy) 0%, #17477f 50%, var(--blue) 100%);
    color: var(--white); font-size: 16px; line-height: 20px;
    text-align: center; padding-top: 8px;
  }
</style>
</head>
<body>

<section class="card card--front" aria-label="Business card front">
  <div class="brand"><span class="brand__dot"></span><span class="brand__name">Clearbrook Optics</span></div>

  <div class="doctor">
    <p class="doctor__name">Dr Tavin R Marquell</p>
    <p class="doctor__role">Associates</p>
  </div>

  <div class="location location--ridgefront">
    <p class="location__name">Ridgefront Brantmart</p>
    <p class="location__phone"><b>P :</b> 509-555-0142</p>
    <p class="location__address">18342 E Fernhollow Ave</p>
  </div>
  <div class="location location--pelham">
    <p class="location__name">Pelham Brantmart</p>
    <p class="location__phone"><b>P :</b> 509-555-0187</p>
    <p class="location__address">4716 W Dunmore Ave</p>
  </div>
  <div class="location location--copper">
    <p class="location__name">Copper Bluff Brantmart</p>
    <p class="location__phone"><b>P :</b> 509-555-0163</p>
    <p class="location__address">3854 S Kettering Rd</p>
  </div>

  <svg class="front-band" viewBox="0 0 672 28" aria-hidden="true">
    <defs>
      <linearGradient id="bandBlue" x1="0" x2="1">
        <stop offset="0" stop-color="#1f2d5c"/>
        <stop offset="1" stop-color="#0f6fae"/>
      </linearGradient>
    </defs>
    <polygon points="328,10 672,10 672,28 342,28" fill="#8f8f8f"/>
    <polygon points="268,0 302,0 330,28 296,28" fill="url(#bandBlue)"/>
    <polygon points="0,0 256,0 278,28 0,28" fill="url(#bandBlue)"/>
  </svg>
  <p class="front-band__url">www.clearbrookoptix.example</p>
</section>

<section class="card card--back" aria-label="Business card back">
  <h2 class="reminder__title">Appointment Reminder</h2>
  <div class="brand"><span class="brand__dot"></span><span class="brand__name">Clearbrook Optics</span></div>

  <div class="field field--name">Patient`s Name:</div>
  <div class="field field--date">Date:<span class="field__time">Time:</span></div>
  <div class="field field--purpose">Purpose:</div>

  <ul class="days">
    <li class="day day--mon"><span class="day__box"></span>Mon</li>
    <li class="day day--tue"><span class="day__box"></span>Tues</li>
    <li class="day day--wed"><span class="day__box"></span>Wed</li>
    <li class="day day--thu"><span class="day__box"></span>Thur</li>
    <li class="day day--fri"><span class="day__box"></span>Fri</li>
  </ul>

  <p class="back-url">www.clearbrookoptix.example</p>
  <div class="back-rule"></div>
  <p class="back-band">We value your time and that of other guests and a 24 hr notice<br>is reqired if you are not able to keep your appointment</p>
</section>

</body>
</html>
```